Property Finance Company - Orbin Funding Limited

Background: Orbin Funding Group Limited is a private property finance company. Orbin Funding Group has capital to directly fund first mortgage, mezzanine and preferred equity financing. We also acquire performing, sub-performing and distressed debt.

Orbin Fundings management philosophy emphasises expertise, innovation, wisdom, honesty and competitiveness. Orbin Funding are not finance brokers - we provide debt funding to the commercial property and residential development sectors. Our process is built from experience and cumutavely Orbin Fundings Directors have in excess of 60 years wisdom.

The aim of the website will be to increase brand awareness, provide clients with comfort around our level of skill and background on who we are, generate more sales, and provide examples of projects that we have funded.

The website is a new product launch, and we need to use our Orbin Funding logo that has just been designed. We like a dark background, and either black/silver/grey/ jade green, or black/gold/jade green colours.

Our unique advantages are that we have fast turnaround times, we can solve clients funding problems and we know what we are doing. Our target audience will be viewing the website on both desktop and mobile devices.

We would like to have the following pages:

Home
About
Team
Services
Project Experience
Contact

Competitors Website: http://www.tarvolo.example/

We would also like to have the option of video footage in our website, as you can see in our competitors website.

Overall we want a really slick, elegant but modern website that is better than www.tarvolo.example

Target Market(s)

Finance borrowers, property developers, accountants, lawyers, businesspeople, high net worth people

Industry/Entity Type

Finance

Requirements
Must have
• Please see project description
Nice to have
Should not have

```html
<!DOCTYPE html>
<html lang="en">
<head>
<meta charset="utf-8">
<title>Orbin Funding Group Limited</title>
<link rel="stylesheet" href="https://fonts.googleapis.com/css2?family=Montserrat:wght@300;400;600;700&family=Playfair+Display:wght@400&display=swap">
<style>
:root{
  --bg:#121212;
  --bg-deep:#0d0d0d;
  --green:#16a05c;
  --grey-bar:#5a5a5a;
  --text:#ffffff;
  --muted:#9a9a9a;
  --line:#3a3a3a;
  --field-line:#6a6a6a;
}
*{box-sizing:border-box;margin:0;padding:0}
html,body{width:1200px;height:3622px;overflow:hidden}
body{background:var(--bg);color:var(--text);font-family:"Montserrat",sans-serif;position:relative}
.abs{position:absolute}
.center{left:0;width:1200px;text-align:center}

/* nav */
.site-nav{top:0;left:0;width:1200px;height:97px;background:rgba(40,40,40,.75);z-index:2}
.nav-link{position:absolute;top:44px;font-size:13px;font-weight:700;letter-spacing:.5px;text-transform:uppercase}
.nav-link.active::after{content:"";position:absolute;left:0;right:0;bottom:-22px;height:3px;background:var(--green)}
.brand{position:absolute;top:18px;left:520px;width:160px;text-align:center}
.brand-dot{display:block;width:26px;height:26px;border-radius:50%;background:#d8d8d8;margin:0 auto 5px}
.brand-name{font-family:"Playfair Display",serif;font-size:12px;letter-spacing:1px;color:#e8e8e8}

/* hero */
.hero{top:0;left:0;width:1200px;height:623px;background:linear-gradient(180deg,#2c3036 0%,#3a3d42 40%,#4a3a2c 75%,#1e1f22 100%)}
.play{top:261px;left:547px}
.hero-title{top:402px;font-size:36px;font-weight:600;letter-spacing:1px}
.hero-sub{top:455px;font-size:20px;font-weight:600;letter-spacing:.5px}

/* section heads */
.section-title{font-family:"Playfair Display",serif;font-size:48px;font-weight:400;letter-spacing:1px}
.divider{left:510px;width:180px;height:30px}
.divider::before,.divider::after{content:"";position:absolute;top:14px;width:65px;height:1px;background:#9a9a9a}
.divider::before{left:0}.divider::after{right:0}
.divider span{position:absolute;left:78px;top:3px;width:24px;height:24px;border-radius:50%;background:#8a8a8a}
.rule{left:300px;width:600px;height:1px;background:linear-gradient(90deg,transparent,var(--line),transparent)}

/* services */
.service{width:220px;text-align:center}
.service svg{display:block;margin:0 auto}
.service-label{margin-top:14px;font-size:13px;font-weight:700;letter-spacing:.5px}

/* about */
.about-bg{top:1122px;left:0;width:1200px;height:640px;background:linear-gradient(180deg,#3a3a3a 0%,#2a2a2a 55%,var(--bg) 100%)}
.about-text{top:1330px;left:145px;width:910px;text-align:center;font-size:13px;font-weight:300;line-height:29px;color:#c8c8c8}
.about-text p+p{margin-top:22px}

/* provide cards */
.card{width:430px;height:353px}
.card-image{width:430px;height:278px}
.card-label{height:75px;display:flex;align-items:center;justify-content:center;font-size:13px;font-weight:700;letter-spacing:.5px}

/* projects */
.project{top:2436px;height:253px}
.project-feature{background:rgba(22,160,92,.9)}
.project-feature h3{font-size:14px;font-weight:700;margin-top:78px}
.project-feature p{font-size:11px;line-height:17px;margin:12px auto 0;width:250px}
.project-btn{display:inline-block;margin-top:14px;background:#fff;color:#333;font-size:10px;font-weight:600;padding:7px 15px}

/* contact */
.field{border:1px solid var(--field-line);height:53px;width:430px;padding:18px 14px;font-size:11px;font-weight:600;letter-spacing:.5px;color:#cfcfcf}
.field-message{width:432px;height:205px}
.submit{top:3240px;left:476px;width:248px;height:53px;background:var(--green);display:flex;align-items:center;justify-content:center;font-size:13px;font-weight:700;letter-spacing:.5px}

/* footer */
.footer-brand{top:3440px;left:520px;width:160px;text-align:center}
.footer-nav{top:3537px;font-size:11px;font-weight:700;letter-spacing:.5px}
.footer-nav a{color:var(--text);text-decoration:none;margin:0 24px}
.copyright{top:3576px;font-size:10px;font-weight:700;letter-spacing:.5px}
</style>
</head>
<body>

<div class="abs hero" role="img" aria-label="Upward view of glass office towers with warm sunlight"></div>

<nav class="abs site-nav">
  <span class="nav-link active" style="left:188px">Home</span>
  <span class="nav-link" style="left:275px">About</span>
  <span class="nav-link" style="left:370px">Team</span>
  <div class="brand"><span class="brand-dot"></span><span class="brand-name">ORBIN FUNDING</span></div>
  <span class="nav-link" style="left:712px">Services</span>
  <span class="nav-link" style="left:828px">Project Experience</span>
  <span class="nav-link" style="left:1036px">Contact</span>
</nav>

<svg class="abs play" width="106" height="106" viewBox="0 0 106 106" aria-hidden="true">
  <circle cx="53" cy="53" r="49" fill="none" stroke="#16a05c" stroke-width="5"/>
  <path d="M42 32 L74 53 L42 74 Z" fill="none" stroke="#16a05c" stroke-width="5" stroke-linejoin="round"/>
</svg>
<h1 class="abs center hero-title">ORBIN FUNDING GROUP LIMITED</h1>
<p class="abs center hero-sub">Private property finance company</p>

<!-- services -->
<h2 class="abs center section-title" style="top:710px">SERVICES</h2>
<div class="abs divider" style="top:786px"><span></span></div>

<div class="abs service" style="left:131px;top:870px">
  <svg width="120" height="110" viewBox="0 0 120 110" aria-hidden="true">
    <path d="M14 40 L60 8 L106 40 Z" fill="#fff"/>
    <rect x="22" y="40" width="76" height="36" fill="#16a05c"/>
    <rect x="34" y="50" width="16" height="14" fill="#fff"/>
    <rect x="68" y="52" width="14" height="24" fill="#fff"/>
    <path d="M10 96 L40 84 L70 88 L96 78 Q108 76 106 86 L70 104 L10 104 Z" fill="none" stroke="#fff" stroke-width="4" stroke-linejoin="round"/>
  </svg>
  <div class="service-label">MORTGAGE</div>
</div>

<div class="abs service" style="left:479px;top:870px">
  <svg width="120" height="110" viewBox="0 0 120 110" aria-hidden="true">
    <rect x="18" y="66" width="18" height="38" fill="#fff"/>
    <rect x="42" y="54" width="18" height="50" fill="#fff"/>
    <rect x="66" y="46" width="18" height="58" fill="#fff"/>
    <rect x="90" y="60" width="16" height="44" fill="#fff"/>
    <path d="M14 56 L40 34 L58 44 L86 16" fill="none" stroke="#fff" stroke-width="4"/>
    <path d="M76 14 L88 12 L88 24" fill="none" stroke="#fff" stroke-width="4"/>
    <circle cx="96" cy="16" r="13" fill="#16a05c"/>
    <text x="96" y="22" text-anchor="middle" font-family="Montserrat,sans-serif" font-weight="700" font-size="16" fill="#fff">$</text>
  </svg>
  <div class="service-label">MEZZANINE</div>
</div>

<div class="abs service" style="left:846px;top:870px">
  <svg width="120" height="110" viewBox="0 0 120 110" aria-hidden="true">
    <path d="M14 36 L60 8 L106 36 Z" fill="none" stroke="#fff" stroke-width="4" stroke-linejoin="round"/>
    <circle cx="60" cy="26" r="6" fill="#16a05c"/>
    <rect x="16" y="38" width="88" height="8" fill="#fff"/>
    <rect x="24" y="50" width="10" height="38" fill="#fff"/>
    <rect x="44" y="50" width="10" height="38" fill="#fff"/>
    <rect x="66" y="50" width="10" height="38" fill="#fff"/>
    <rect x="86" y="50" width="10" height="38" fill="#fff"/>
    <rect x="12" y="92" width="96" height="8" fill="#fff"/>
  </svg>
  <div class="service-label">EQUITY FINANCING</div>
</div>

<!-- about -->
<div class="abs about-bg" role="img" aria-label="Businessman in a suit looking at his phone, dimmed"></div>
<h2 class="abs center section-title" style="top:1195px">ABOUT</h2>
<div class="abs divider" style="top:1269px"><span></span></div>
<div class="abs about-text">
  <p>Orbin Funding Group Limited is a private property finance company. Orbin Funding Group has capital to directly fund first mortgage, mezzanine and preferred equity financing. We also acquire performing, sub-performing and distressed debt.</p>
  <p>Orbin Fundings management philosophy emphasises expertise, innovation, wisdom, honesty and competitiveness. Orbin Funding are not finance brokers - we provide debt funding to the commercial property and residential development sectors. Our process is built from experience and cumutavely Orbin Fundings Directors have in excess of 60 years wisdom.</p>
</div>
<div class="abs rule" style="top:1564px"></div>

<h2 class="abs center section-title" style="top:1638px">WHAT WE PROVIDE</h2>
<div class="abs divider" style="top:1718px"><span></span></div>

<div class="abs card" style="left:157px;top:1822px">
  <div class="card-image" role="img" aria-label="Glass office tower seen from below against a blue sky" style="background:linear-gradient(160deg,#6fa8d8 0%,#3f7cae 45%,#2f6b6a 100%)"></div>
  <div class="card-label" style="background:var(--grey-bar)">COMMERCIAL PROPERTY</div>
</div>
<div class="abs card" style="left:608px;top:1822px">
  <div class="card-image" role="img" aria-label="Modern residential house lit at dusk" style="background:linear-gradient(180deg,#3c4a78 0%,#4e5677 50%,#6b5a4a 100%)"></div>
  <div class="card-label" style="background:var(--green)">RESIDENTIAL PROPERTY</div>
</div>

<div class="abs rule" style="top:2238px"></div>
<h2 class="abs center section-title" style="top:2266px">PROJECT EXPERIENCE</h2>
<div class="abs divider" style="top:2346px"><span></span></div>

<div class="abs project project-feature" style="left:0;width:398px;text-align:center">
  <h3>PROJECT 1</h3>
  <p>Neque porro quisquam est qui dolorem ipsum quia dolor sit amet, consectetur</p>
  <span class="project-btn">VIEW DETAILS</span>
</div>
<div class="abs project" style="left:398px;width:401px;background:linear-gradient(135deg,#d9dde0 0%,#8a96a6 50%,#4f5a6c 100%)" role="img" aria-label="Business people signing papers at a laptop"></div>
<div class="abs project" style="left:799px;width:401px;background:linear-gradient(135deg,#4c5a6a 0%,#8a7a70 50%,#c89a8a 100%)" role="img" aria-label="Pink piggy bank on a table with soft lights"></div>

<div class="abs rule" style="top:2766px"></div>
<h2 class="abs center section-title" style="top:2807px">CONTACT US</h2>
<div class="abs divider" style="top:2882px"><span></span></div>

<div class="abs field" style="left:157px;top:2986px">NAME</div>
<div class="abs field" style="left:157px;top:3063px">E-MAIL</div>
<div class="abs field" style="left:157px;top:3138px">PHONE</div>
<div class="abs field field-message" style="left:606px;top:2986px">MESSAGE</div>
<div class="abs submit">SUBMIT</div>

<div class="abs rule" style="top:3399px"></div>
<div class="abs footer-brand"><span class="brand-dot"></span><span class="brand-name">ORBIN FUNDING</span></div>
<nav class="abs center footer-nav">
  <a>HOME</a><a>ABOUT</a><a>TEAM</a><a>SERVICES</a><a>PROJECT EXPERIENCE</a><a>CONTACT</a>
</nav>
<p class="abs center copyright">© 2017 COMPANY NAME | ALL RIGHTS RESERVED</p>

</body>
</html>
```